Makers' Hollow - Landing page for small and large screen

Makers’ Hollow gives you the space you need to take your side project from idea to reality.

With three days of focused work, it’s a place for you iron out the details of your business idea away from the distractions of the city.

The full copy and structure is here:
https://www.makershollow.co.uk/landing

What it needs, a touch of colour.

Target Market(s)

25-35 working in digital industry, software developer, a UI or UX designer

Number of Pages Required

1 page

Font styles to use
Sans Serif

Colors
0292cd
33b8a4
86cfc6
fdf9cf
ec1f27

Requirements
Should not have
• gradients or too much images

```html
<!DOCTYPE html>
<html lang="en">
<head>
<meta charset="utf-8">
<title>Makers' Hollow</title>
<link href="https://fonts.googleapis.com/css2?family=Lato:wght@400;700;900&display=swap" rel="stylesheet">
<style>
  :root{
    --blue:#0292cd;
    --heading-blue:#1a8ac8;
    --teal:#2aa98f;
    --teal-light:#86cfc6;
    --cream:#fbf6c5;
    --red:#ec1f27;
    --text:#3b3b3b;
    --white:#ffffff;
    --border:#cfcfcf;
  }
  *{box-sizing:border-box;margin:0;padding:0}
  html,body{width:1200px;height:2586px;overflow:hidden}
  body{font-family:'Lato',sans-serif;color:var(--text);background:var(--white)}
  section,header,footer{position:relative;width:1200px}
  .btn{display:inline-flex;align-items:center;justify-content:center;width:154px;height:42px;background:var(--teal);color:var(--white);font-weight:700;font-size:18px;text-decoration:none}

  .site-header{height:95px;background:linear-gradient(90deg,var(--blue),var(--teal));color:var(--white)}
  .brand{position:absolute;left:74px;top:16px}
  .brand-name{font-size:32px;font-weight:700;line-height:38px}
  .brand-tag{font-size:17px;line-height:20px;padding-left:2px}
  .main-nav{position:absolute;right:73px;top:36px;display:flex;gap:44px;font-size:16px;font-weight:700;letter-spacing:.3px}

  .hero{height:505px;background:linear-gradient(100deg,#3c4652 0%,#8a8f96 35%,#c9c4bd 60%,#6b6f74 100%);text-align:center;color:var(--white)}
  .hero-title{position:absolute;left:0;right:0;top:283px;font-size:70px;font-weight:900;line-height:80px;text-shadow:0 2px 6px rgba(0,0,0,.3)}
  .hero-sub{position:absolute;left:0;right:0;top:362px;font-size:31px;font-weight:700;line-height:38px}

  .intro{height:402px}
  .art{position:absolute}
  .intro .art{left:74px;top:72px;width:348px;height:233px;background:linear-gradient(135deg,#e8f2f8,#f7d9b8 55%,#cfe7f5)}
  .intro-copy{position:absolute;left:448px;top:55px;width:690px}
  h2{font-weight:400;color:var(--heading-blue);font-size:28px;line-height:34px}
  p{font-size:16px;line-height:26px}
  .intro-copy h2{margin-bottom:12px}
  .intro-copy p{margin-bottom:6px}
  .intro-copy .btn{margin-top:24px}

  .focus{height:341px;background:var(--cream)}
  .focus-copy{position:absolute;left:76px;top:34px;width:690px}
  .focus-copy h2{margin-bottom:12px}
  .focus .art{left:810px;top:29px;width:276px;height:284px;background:radial-gradient(circle at 50% 45%,#f7c842 0 35%,#cfe9ef 36% 60%,var(--cream) 75%)}
  .focus-copy .btn{margin-top:30px}

  .benefits{height:293px;text-align:center}
  .benefits h2{position:absolute;left:0;right:0;top:46px}
  .benefit-list{position:absolute;top:106px;list-style:none;text-align:left;font-size:15.5px}
  .benefit-list li{display:flex;align-items:center;gap:20px;height:37px}
  .benefit-list svg{width:16px;height:16px;flex:none}
  .list-left{left:172px}
  .list-right{left:638px}

  .stay{height:229px;background:var(--teal);color:var(--white)}
  .stay .art{left:141px;top:22px;width:212px;height:190px;border-radius:50%;background:radial-gradient(circle,#fbe3a2 0 60%,#f7d27a 100%)}
  .stay-copy{position:absolute;left:433px;top:44px;width:710px}
  .stay-copy h3{font-weight:400;font-size:26px;line-height:32px;margin-bottom:18px}
  .stay-copy p{font-size:15.5px;line-height:26px}

  .organisers{height:376px;text-align:center}
  .organisers h2{position:absolute;left:0;right:0;top:44px}
  .card{position:absolute;top:106px;width:512px;height:220px;border:1.5px solid var(--border);text-align:left}
  .card-left{left:74px}
  .card-right{left:614px}
  .avatar{position:absolute;left:17px;top:24px;width:76px;height:76px;border-radius:50%;background:#3a3a3a}
  .card h3{position:absolute;left:110px;top:20px;color:var(--red);font-size:21px;font-weight:700}
  .card p{position:absolute;left:110px;top:48px;width:382px;font-size:15.5px;line-height:26px}

  .feedback{height:221px;background:var(--cream);text-align:center}
  .feedback h2{padding-top:44px}
  .feedback p{margin-top:14px;font-size:16px}
  .feedback .btn{margin-top:20px}

  .site-footer{height:129px;text-align:center}
  .copyright{padding-top:38px;font-size:12.5px;color:#222}
  .social{display:flex;justify-content:center;gap:18px;margin-top:16px}
  .social span{width:18px;height:18px;border-radius:50%;background:#2b2b2b}
</style>
</head>
<body>
  <header class="site-header">
    <div class="brand">
      <div class="brand-name">Makers' Hollow</div>
      <div class="brand-tag">create. connect. collaborate</div>
    </div>
    <nav class="main-nav"><span>HOME</span><span>ABOUT US</span><span>SERVICES</span><span>BLOG</span><span>CONTACT US</span></nav>
  </header>

  <section class="hero" role="img" aria-label="Photo of smiling people collaborating in a bright office">
    <h1 class="hero-title">MAKERS' HOLLOW</h1>
    <div class="hero-sub">CREATE. CONNECT. COLLABORATE</div>
  </section>

  <section class="intro">
    <div class="art" role="img" aria-label="Illustration of creatives working together around a large screen"></div>
    <div class="intro-copy">
      <h2>Makers’ Hollow gives you the space you need to take your side project from idea to reality.</h2>
      <p>Calling all creatives! Whether you’re a software developer, a UI or UX designer, a product creator or an artworker, you’ll know only too well that great work rarely materialises when you’re in the wrong environment.</p>
      <p>Phones buzzing. Emails pinging. Video calls incoming...distractions are everywhere – and they do nothing for your motivation.</p>
      <a class="btn" href="#">Read More</a>
    </div>
  </section>

  <section class="focus">
    <div class="focus-copy">
      <h2>With three days of focused work, it’s a place for you iron out the details of your business idea away from the distractions of the city.</h2>
      <p>Whatever stage your side hustle’s at, we’re here to help it thrive. Our warm and friendly Retreat is just that: a place to create, connect and collaborate with likeminded folks. Oh, and there’s yoga, meditation, healthy meals and snacks, and all the feedback you need to power on through.</p>
      <a class="btn" href="#">Read More</a>
    </div>
    <div class="art" role="img" aria-label="Illustration of a light bulb with an atom and idea icons"></div>
  </section>

  <section class="benefits">
    <h2>Join the Retreat and enjoy:</h2>
    <ul class="benefit-list list-left">
      <li><svg viewBox="0 0 16 16"><circle cx="8" cy="8" r="8" fill="#ec1f27"/><path d="M4.5 8.3l2.3 2.3 4.7-4.8" stroke="#fff" stroke-width="2" fill="none"/></svg>Three, full days of distraction-free work</li>
      <li><svg viewBox="0 0 16 16"><circle cx="8" cy="8" r="8" fill="#ec1f27"/><path d="M4.5 8.3l2.3 2.3 4.7-4.8" stroke="#fff" stroke-width="2" fill="none"/></svg>A chance to hone your side project away from the office</li>
      <li><svg viewBox="0 0 16 16"><circle cx="8" cy="8" r="8" fill="#ec1f27"/><path d="M4.5 8.3l2.3 2.3 4.7-4.8" stroke="#fff" stroke-width="2" fill="none"/></svg>The opportunity to collaborate with likeminded creatives</li>
      <li><svg viewBox="0 0 16 16"><circle cx="8" cy="8" r="8" fill="#ec1f27"/><path d="M4.5 8.3l2.3 2.3 4.7-4.8" stroke="#fff" stroke-width="2" fill="none"/></svg>Good, honest feedback and insight from fellow attendees</li>
    </ul>
    <ul class="benefit-list list-right">
      <li><svg viewBox="0 0 16 16"><circle cx="8" cy="8" r="8" fill="#ec1f27"/><path d="M4.5 8.3l2.3 2.3 4.7-4.8" stroke="#fff" stroke-width="2" fill="none"/></svg>Daily yoga and meditation to help fuel your ideas</li>
      <li><svg viewBox="0 0 16 16"><circle cx="8" cy="8" r="8" fill="#ec1f27"/><path d="M4.5 8.3l2.3 2.3 4.7-4.8" stroke="#fff" stroke-width="2" fill="none"/></svg>Three, nutritious and delicious meals a day</li>
      <li><svg viewBox="0 0 16 16"><circle cx="8" cy="8" r="8" fill="#ec1f27"/><path d="M4.5 8.3l2.3 2.3 4.7-4.8" stroke="#fff" stroke-width="2" fill="none"/></svg>Healthy, low-sugar snacks to get you through the day</li>
    </ul>
  </section>

  <section class="stay">
    <div class="art" role="img" aria-label="Illustration of a folded map with a location pin and compass"></div>
    <div class="stay-copy">
      <h3>Where You’ll be Staying</h3>
      <p>A retreat wouldn’t be a retreat without a calm, peaceful and picturesque location. It’s the reason we’re working hard behind the scenes to find the ideal spot to host you. Of course, it’ll have Wi-Fi/4G Internet – but it’ll also be somewhere that will allow for maximum creativity.</p>
    </div>
  </section>

  <section class="organisers">
    <h2>Meet Your Retreat Organisers</h2>
    <article class="card card-left">
      <div class="avatar" role="img" aria-label="Portrait photo of organiser Tomas Varga"></div>
      <h3>Tomas Varga</h3>
      <p>A software engineer in London, Tomas knows only too well the challenges faced by creatives; it’s the reason he’s organised the Makers’ Hollow, to give everyone the space and time to do their best work. Armed with his trusty camera, photographer Tomas is also a biohacker enthusiast and a thoroughly good egg...”</p>
    </article>
    <article class="card card-right">
      <div class="avatar" role="img" aria-label="Portrait photo of organiser Elena Marin"></div>
      <h3>Elena Marin</h3>
      <p>An internationally-certified yoga teacher, Elena loves connecting with people and discovering how she can help them get the best out of their day – and their work. Giving attendees the time to enjoy some self-care in the form of a spot of gentle yoga, animal lover Elena will help you unleash those ideas!</p>
    </article>
  </section>

  <section class="feedback">
    <h2>What do you think?</h2>
    <p>Sound good? Keen to know more? Share some feedback via the button below and we can hone the Retreat to suit you.</p>
    <a class="btn" href="#">Read More</a>
  </section>

  <footer class="site-footer">
    <div class="copyright">Copyright © 2019. Company Name All Right Reserved</div>
    <div class="social" aria-label="Social links"><span></span><span></span><span></span><span></span><span></span><span></span></div>
  </footer>
</body>
</html>
```